Birchline Septic Solutions

Would like to see some single sided ones but would also like to see some double sided with one sided only being the logo. Owners name is Colin Vandro. Phone number is 555-214-0387
Services are pumping, inspections, installs, and repairs

Contact Information for Business Card

555-241-0387 Colin Vandro Hollisport, OH

```html
<!DOCTYPE html>
<html lang="en">
<head>
<meta charset="utf-8">
<title>Birchline Septic Solutions — Business Cards</title>
<link href="https://fonts.googleapis.com/css2?family=Arimo:wght@400;700&display=swap" rel="stylesheet">
<style>
  :root {
    --backdrop: #e9e9e9;
    --card-white: #ffffff;
    --card-dark: #2a2a2a;
    --ink: #2b2b2b;
    --ink-soft: #8a8a8a;
    --teal: #2bbfb3;
    --emboss: #3b3b3b;
  }
  * { box-sizing: border-box; margin: 0; padding: 0; }
  html, body {
    width: 1200px; height: 802px; overflow: hidden;
    background: var(--backdrop);
    font-family: "Arimo", Arial, sans-serif;
  }
  .sheet {
    position: relative; width: 1200px; height: 802px;
    display: flex; align-items: center; justify-content: center; gap: 44px;
  }
  .card {
    position: relative; width: 528px; height: 302px; overflow: hidden;
    border-bottom: 5px solid var(--teal);
    box-shadow: 0 8px 22px rgba(0,0,0,0.18);
  }
  .card--front { background: var(--card-white); }
  .card--back { background: var(--card-dark); }

  .corner-tab {
    position: absolute; top: 0; right: 22px;
    width: 18px; height: 26px; background: var(--teal);
  }
  .owner {
    position: absolute; top: 26px; right: 52px; text-align: right;
  }
  .owner__name {
    color: var(--teal); font-weight: 700; font-size: 22px; letter-spacing: 0.5px;
  }
  .owner__role { color: var(--ink-soft); font-size: 14px; margin-top: 2px; }

  .scenery {
    position: absolute; right: 0; bottom: 0; width: 250px; height: 215px;
    background: linear-gradient(160deg, #5a5a5a 0%, #2b2b2b 55%, #1f1f1f 100%);
  }

  .brand {
    position: absolute; left: 30px; top: 104px; width: 240px;
  }
  .brand__name {
    color: var(--ink); font-weight: 700; font-size: 27px; line-height: 1.1;
    text-transform: uppercase; letter-spacing: 1px;
  }

  .contact {
    position: absolute; left: 30px; bottom: 34px;
    color: var(--ink-soft); font-size: 16px; line-height: 1.5;
  }
  .contact__phone {
    display: flex; align-items: center; gap: 7px;
    color: var(--ink); font-weight: 700; font-size: 17px;
  }
  .contact__phone svg { width: 14px; height: 14px; }

  .back-brand {
    position: absolute; inset: 0;
    display: flex; align-items: center; justify-content: center; text-align: center;
    color: var(--emboss); font-weight: 700; font-size: 34px; line-height: 1.15;
    text-transform: uppercase; letter-spacing: 2px; padding: 0 60px;
  }
</style>
</head>
<body>
  <main class="sheet">
    <section class="card card--front" aria-label="Business card front">
      <div class="corner-tab"></div>
      <div class="owner">
        <p class="owner__name">COLIN VANDRO</p>
        <p class="owner__role">Owners</p>
      </div>
      <div class="scenery" role="img" aria-label="Dark silhouette of rocky mountain peaks with pine trees along the base"></div>
      <div class="brand">
        <p class="brand__name">Birchline Septic Solutions</p>
      </div>
      <div class="contact">
        <p class="contact__city">Hollisport, OH</p>
        <p class="contact__phone">
          <svg viewBox="0 0 16 16" aria-hidden="true">
            <circle cx="8" cy="8" r="7" fill="none" stroke="#2bbfb3" stroke-width="2"/>
            <path d="M5.5 4.5 L7 6 L6.2 7 Q7 8.8 9 9.8 L10 9 L11.5 10.5 L10.5 11.6 Q6 10.8 4.4 5.6 Z" fill="#2bbfb3"/>
          </svg>
          555-214-0387
        </p>
      </div>
    </section>

    <section class="card card--back" aria-label="Business card back">
      <p class="back-brand">Birchline Septic Solutions</p>
    </section>
  </main>
</body>
</html>
```